Stonebridge Building and Projects business cards

A business card with watermark background (construction work)

Company logo attached

Home improvement projects
House renovations
Bathroom and kitchen renovations
House extensions
New builds and granny flats

Director Omar Haddani
(Phone number)
omar@sbpbuilding.com.au
(Instagram logo) sbp_building

```html
<!DOCTYPE html>
<html lang="en">
<head>
<meta charset="utf-8">
<title>Stonebridge Building and Projects – Business Cards</title>
<link href="https://fonts.googleapis.com/css2?family=Montserrat:wght@700&family=Roboto:wght@400;500;700&display=swap" rel="stylesheet">
<style>
  :root {
    --brand-blue: #1677c5;
    --brand-blue-dark: #0f5f9f;
    --band-grey: #3e4045;
    --ink: #2b2d31;
    --muted-grey: #9a9ca0;
    --paper: #f7f7f7;
    --stage: #e4e5e7;
    --white: #ffffff;
  }
  * { box-sizing: border-box; margin: 0; padding: 0; }
  html, body { width: 1200px; height: 1050px; overflow: hidden; }
  body {
    background: var(--stage);
    font-family: "Roboto", Arial, sans-serif;
    position: relative;
  }
  .card {
    position: absolute;
    left: 180px;
    width: 840px;
    height: 480px;
    border-radius: 34px;
    overflow: hidden;
    box-shadow: 0 8px 22px rgba(0,0,0,0.18);
  }

  /* Front */
  .card-front { top: 30px; background: var(--brand-blue); color: var(--white); }
  .front-logo {
    position: absolute; top: 70px; left: 0; width: 100%;
    text-align: center;
  }
  .wordmark {
    font-family: "Montserrat", Arial, sans-serif;
    font-weight: 700;
    font-size: 62px;
    letter-spacing: 1px;
    line-height: 1;
  }
  .wordmark-sub {
    font-family: "Montserrat", Arial, sans-serif;
    font-weight: 700;
    font-size: 24px;
    margin-top: 10px;
    letter-spacing: 1px;
  }
  .tagline {
    display: inline-block;
    margin-top: 14px;
    font-size: 24px;
    font-weight: 500;
    border-bottom: 2px solid currentColor;
    padding-bottom: 2px;
  }
  .services-band {
    position: absolute; top: 300px; left: 0; width: 100%; height: 100px;
    background: var(--band-grey);
    display: flex; flex-direction: column; justify-content: center; align-items: center;
    gap: 10px;
    font-size: 21px;
  }
  .services-band .sep { margin: 0 12px; opacity: 0.8; }
  .front-links {
    position: absolute; top: 420px; left: 0; width: 100%;
    display: flex; justify-content: center; gap: 48px;
    font-size: 21px;
  }
  .link-item { display: flex; align-items: center; gap: 10px; }
  .dot { width: 14px; height: 14px; border-radius: 50%; background: var(--white); display: inline-block; }

  /* Back */
  .card-back { top: 540px; background: var(--paper); color: var(--ink); }
  .back-logo { position: absolute; top: 60px; left: 60px; color: var(--brand-blue); }
  .back-logo .wordmark { font-size: 44px; }
  .back-logo .wordmark-sub { font-size: 17px; margin-top: 6px; }
  .back-logo .tagline { font-size: 17px; margin-top: 8px; }
  .person { position: absolute; top: 220px; left: 60px; }
  .person-name { color: var(--brand-blue); font-weight: 700; font-size: 36px; }
  .person-role { font-size: 21px; margin-top: 4px; }
  .contacts { position: absolute; top: 310px; left: 60px; list-style: none; }
  .contacts li { display: flex; align-items: center; gap: 14px; font-size: 21px; height: 34px; }
  .contacts svg { width: 20px; height: 20px; flex: none; }
  .contacts .dot { background: var(--brand-blue); width: 16px; height: 16px; margin: 0 2px; }
  .texture-panel {
    position: absolute; top: 40px; right: 230px; width: 180px; height: 420px;
    background: linear-gradient(160deg, rgba(154,156,160,0.55), rgba(154,156,160,0.15));
    transform: skewX(-12deg);
  }
  .accent-block {
    position: absolute; top: 0; right: 0; width: 220px; height: 100%;
    background: var(--brand-blue);
  }
</style>
</head>
<body>

<section class="card card-front" aria-label="Business card front">
  <div class="front-logo">
    <div class="wordmark">Stonebridge</div>
    <div class="wordmark-sub">Building and Projects</div>
    <div class="tagline">Built to last!</div>
  </div>
  <div class="services-band">
    <p>Home Improvement Projects<span class="sep">|</span>House Renovations<span class="sep">|</span>House Extensions</p>
    <p>Bathroom &amp; Kitchen Renovations<span class="sep">|</span>New Builds &amp; Granny Flats</p>
  </div>
  <div class="front-links">
    <span class="link-item"><span class="dot"></span>sbp_building</span>
    <span class="link-item">
      <svg width="20" height="20" viewBox="0 0 20 20" fill="none" stroke="#fff" stroke-width="1.6"><circle cx="10" cy="10" r="8.5"/><ellipse cx="10" cy="10" rx="3.8" ry="8.5"/><path d="M1.5 10h17M3 5.5h14M3 14.5h14"/></svg>
      sbpbuilding.com.au
    </span>
  </div>
</section>

<section class="card card-back" aria-label="Business card back">
  <div class="texture-panel" role="img" aria-label="Grey tiled construction texture"></div>
  <div class="accent-block"></div>
  <div class="back-logo">
    <div class="wordmark">Stonebridge</div>
    <div class="wordmark-sub">Building and Projects</div>
    <div class="tagline">Built to last!</div>
  </div>
  <div class="person">
    <h1 class="person-name">Omar Haddani</h1>
    <p class="person-role">Managing Director</p>
  </div>
  <ul class="contacts">
    <li><svg viewBox="0 0 20 20" fill="none" stroke="#1677c5" stroke-width="1.8"><path d="M5 2.5l3 3.5-1.8 2a10 10 0 0 0 5.8 5.8l2-1.8 3.5 3-1.7 2.3C9 17 3 11 2.7 4.2z"/></svg>0412 555 308</li>
    <li><svg viewBox="0 0 20 20" fill="none" stroke="#1677c5" stroke-width="1.8"><rect x="2" y="4" width="16" height="12" rx="1.5"/><path d="M2.5 5l7.5 6 7.5-6"/></svg>omar@sbpbuilding.com.au</li>
    <li><svg viewBox="0 0 20 20" fill="none" stroke="#1677c5" stroke-width="1.6"><circle cx="10" cy="10" r="8.5"/><ellipse cx="10" cy="10" rx="3.8" ry="8.5"/><path d="M1.5 10h17M3 5.5h14M3 14.5h14"/></svg>sbpbuilding.com.au</li>
    <li><span class="dot"></span>sbp_building</li>
  </ul>
</section>

</body>
</html>
```